Easy Marinade Labels for Butchery Store

Need a set of labels designed for a Butchery Shop. They will sit in the top left corner of the packets as a triangle (7cm each side). Easy because the only major requirement is the label name and some small text saying "Please ask in store to see spec sheet for ingredients". Extra points for finding a fun way to incorporate the logo and/or images of food (garlic bulbs, chilli, spices ect) to enhance the label. List of Marinade Names below: GarlicPepper Mint & RosemarySatayBBQChilli Plum & GingerSundried Tomato & BasilBuffaloHoney SoyHoi-SinPer PeriSpicy CajunTeriyakiBlack Bean Ive also attached the logo and an example of how the label might sit on a packet of meat. Thanks

Target Market(s)

Butchery Deli Shop Customers

Industry/Entity Type

Food Store

Font styles to use
Serif
Sans Serif
Decorative
Other font styles liked:
• Fun font that isn't a generic Quellbrix Font?

Colors

Designer to choose colors to be used in the design.

Requirements
Must have
• Product Name
• Small text saying "Please ask in store to see spec sheet for ingredients"
Nice to have
• Photos of ingredients that would match that type of marinade - Chilli, Garlic, Spices.
• Fenly Oak Logo - not essential if it doesn't look good on the label / doesn't fit.

```html
<!DOCTYPE html>
<html lang="en">
<head>
<meta charset="utf-8">
<title>Black Bean Marinade Label</title>
<link rel="stylesheet" href="https://fonts.googleapis.com/css2?family=Open+Sans:wght@800&family=Permanent+Marker&display=swap">
<style>
  :root {
    --paper: #ffffff;
    --frame-yellow: #eefc12;
    --bean-dark: #15151f;
    --bean-navy: #2e3048;
    --bean-slate: #4b4f6a;
    --onion-orange: #f08a2a;
    --onion-cream: #f3c596;
    --shade-black: #000000;
    --label-text: #ffffff;
  }
  html, body {
    margin: 0;
    padding: 0;
    width: 1200px;
    height: 900px;
    overflow: hidden;
    background: var(--paper);
  }
  .canvas {
    display: block;
    width: 1200px;
    height: 900px;
  }
  .product-name {
    font-family: "Permanent Marker", cursive;
    font-size: 92px;
    fill: var(--label-text);
    text-anchor: middle;
    letter-spacing: 2px;
  }
  .spec-note {
    font-family: "Open Sans", sans-serif;
    font-weight: 800;
    font-size: 21px;
    letter-spacing: 2.6px;
    fill: var(--label-text);
    text-anchor: middle;
  }
  .label-frame {
    fill: none;
    stroke: var(--frame-yellow);
    stroke-width: 7;
    stroke-linejoin: miter;
  }
</style>
</head>
<body>
<svg class="canvas" viewBox="0 0 1200 900" xmlns="http://www.w3.org/2000/svg">
  <defs>
    <clipPath id="label-shape">
      <polygon points="620.5,175 146,645 1095,645"/>
    </clipPath>
    <linearGradient id="ingredient-tones" x1="0" y1="1" x2="1" y2="0">
      <stop offset="0" stop-color="var(--onion-cream)"/>
      <stop offset="0.22" stop-color="var(--onion-orange)"/>
      <stop offset="0.42" stop-color="var(--bean-navy)"/>
      <stop offset="0.7" stop-color="var(--bean-slate)"/>
      <stop offset="1" stop-color="var(--bean-dark)"/>
    </linearGradient>
    <linearGradient id="base-shade" x1="0" y1="0" x2="0" y2="1">
      <stop offset="0" stop-color="var(--shade-black)" stop-opacity="0"/>
      <stop offset="1" stop-color="var(--shade-black)" stop-opacity="0.95"/>
    </linearGradient>
  </defs>

  <g class="label" clip-path="url(#label-shape)">
    <rect class="ingredient-photo" role="img" aria-label="Photo of black beans with a peeled onion and orange peppers"
          x="140" y="170" width="960" height="480" fill="url(#ingredient-tones)"/>
    <rect class="base-shade" x="140" y="575" width="960" height="75" fill="url(#base-shade)"/>
  </g>

  <polygon class="label-frame" points="620.5,175 146,645 1095,645"/>

  <text class="product-name" x="632" y="442">BLACK</text>
  <text class="product-name" x="626" y="540">BEAN</text>

  <text class="spec-note" x="621" y="620">PLEASE ASK IN STORE TO SEE SPEC SHEET FOR INGREDIENTS</text>
</svg>
</body>
</html>
```